Brightcoat Painting Services Requires a New Responsive Site

Hi Designers,

Our current website is this www.brightcoatpainting.com.au for some idea.
I made it on Adobe Muse, its very basic.
I would like it to be redesigned to look more professional and also responsive. I actually know how to do html5 and css but I think others will do this much better than me.

I do not need content because I am a copywriter and would like to do all SEO and copy myself.

The most improtant things to remember is that the site cannot use a CMS
and the code needs to be understandable so that I can go in and add content later on and do SEO work.

Also the site requires an additional testimonial page. I would imagine a nice gallery would be a great addition too(something that I can add images too through html. Also in it is important for it to contain those brand images on the front page as it increases authority. I will attach them onto the brief.

Those two files of nearbyfind and tradeleafs are local directories where we have reviews so a placement of those on the testimonail page would make great sense. I will to the href myself.

Anyway, good luck!

I look forward to see your designs :D
Updates

I have just been informed that on this site websites are simply designed and not built (developed) if this is the case please stop working on your designs and spending more time on this project. I REQUIRE DEVELOPMENT ALSO AND HAVE ALREADY CONTACTED SUPPORT.

Target Market(s)

The target market is 30-75 high income earners.

Industry/Entity Type

Painting

Number of Pages Required

5+ page

Font styles to use
Serif
Sans Serif

Requirements
Must have
• attractive gallery, and the brand icons uploaded.
• must be responsive
• web carousel (with the different types of work we do). eg domestic, commercial, industrial etc.
Nice to have
• a little interactivity
• corporate a natural design that goes well with our logo
Should not have
• any content. just write jiberish to fill in the spaces.
• I will be doing all copy and SEO myself.
• More than five pages, bascially the four that already exist plus the testimonail one.

```html
<!DOCTYPE html>
<html lang="en">
<head>
<meta charset="utf-8">
<title>Brightcoat Painting Services</title>
<link rel="stylesheet" href="https://fonts.googleapis.com/css2?family=Open+Sans:wght@400;600;700&display=swap">
<style>
:root{
  --charcoal:#363434;
  --blue:#4fa8e0;
  --steel:#2f6d95;
  --navy:#1f4a66;
  --ink:#333333;
  --grey-text:#555555;
  --band:#ededed;
  --panel:#eeeef0;
  --gallery-bg:#f4f4f4;
  --badge:#1f3f7a;
  --white:#ffffff;
}
*{margin:0;padding:0;box-sizing:border-box}
html,body{width:1200px;height:2432px;overflow:hidden}
body{position:relative;background:var(--white);font-family:"Open Sans",Arial,sans-serif;color:var(--ink)}
.abs{position:absolute}

/* header */
.header-band{left:0;top:0;width:1200px;height:392px;background:var(--charcoal)}
.logo{left:97px;top:24px;width:140px;height:110px}
.logo-mark{position:absolute;left:36px;top:0;width:64px;height:64px;background:var(--blue)}
.logo-name{position:absolute;left:0;top:84px;color:var(--white);font-weight:700;font-size:15px;white-space:nowrap}
.phone{right:100px;top:46px;color:var(--white);font-weight:600;font-size:28px;display:flex;align-items:center;gap:10px}
.nav{top:100px;right:100px;display:flex;gap:36px;list-style:none}
.nav li{color:var(--white);font-size:15px;padding-bottom:12px;position:relative}
.nav li.active::after{content:"";position:absolute;left:-8px;right:-8px;bottom:-4px;height:5px;background:var(--blue)}

/* hero */
.hero{left:97px;top:138px;width:1003px;height:397px;background:var(--panel);overflow:hidden}
.hero-photo{position:absolute;left:0;top:0}
.hero-title{position:absolute;left:587px;top:168px;font-size:31px;font-weight:700;color:var(--ink)}
.hero-title span{color:var(--blue)}
.hero-text{position:absolute;left:587px;top:214px;width:390px;font-size:15px;line-height:24px;color:var(--ink)}
.hero-btn{position:absolute;left:587px;top:280px;width:145px;height:36px;background:var(--blue);border-radius:4px;color:var(--white);font-weight:700;font-size:15px;display:flex;align-items:center;justify-content:center;gap:8px}
.hero-dots{position:absolute;left:921px;top:358px;display:flex;gap:7px}
.hero-dots i{width:11px;height:11px;border-radius:50%;background:var(--charcoal)}
.hero-dots i:first-child{background:var(--blue)}

/* services */
.section-title{left:0;width:1200px;text-align:center;font-size:24px;font-weight:400;color:var(--ink);letter-spacing:.5px}
.service{top:631px;width:243px}
.service-photo{width:243px;height:146px}
.service-name{margin-top:35px;font-size:20px;font-weight:600;color:var(--steel)}
.service-text{margin-top:12px;font-size:12px;line-height:19px;color:var(--ink)}

/* quality band */
.quality{left:0;top:983px;width:1200px;height:313px;background:var(--band);text-align:center;overflow:hidden}
.stars{margin-top:38px;display:flex;justify-content:center;gap:8px}
.quality h2{margin-top:14px;font-size:23px;font-weight:700;color:var(--steel)}
.quality p{margin:14px auto 0;width:840px;font-size:25px;line-height:34px;color:var(--grey-text)}

/* gallery */
.gallery{left:204px;top:1362px;width:789px;height:597px;background:var(--gallery-bg);border:1px solid #dddddd}
.gallery-title{position:absolute;top:26px;width:100%;text-align:center;font-size:24px;font-weight:400}
.gallery-main{position:absolute;left:59px;top:72px;width:670px;height:344px;border:5px solid #e6e6e6}
.gallery-shadow{position:absolute;left:100px;top:418px;width:590px;height:22px;border-radius:50%;background:radial-gradient(ellipse at top,rgba(0,0,0,.35),rgba(0,0,0,0) 70%)}
.thumb{position:absolute;top:460px;width:100px;height:83px;border:2px solid #222}
.arrow{position:absolute;top:490px}

/* partners */
.partner{top:2027px;height:81px;display:flex;align-items:center;justify-content:center;gap:8px;font-size:17px;font-weight:700;color:var(--ink)}

/* footer */
.footer{left:0;top:2132px;width:1200px;height:300px;background:var(--charcoal);color:var(--white)}
.footer h4{position:absolute;top:30px;font-size:13px;font-weight:700;color:var(--blue)}
.footer ul{position:absolute;top:80px;list-style:none;font-size:12px}
.footer ul li{height:30px}
.contact-list li{display:flex;align-items:center;gap:10px}
.social li{display:flex;justify-content:space-between;width:146px;height:37px}
.social i{width:20px;height:20px;border-radius:50%;border:1px solid #3a6f95}
.quote-btn{position:absolute;left:548px;top:179px;width:104px;height:27px;background:var(--blue);border-radius:4px;color:var(--charcoal);font-size:12px;font-weight:700;display:flex;align-items:center;justify-content:center}
.footer-rule{position:absolute;left:0;top:236px;width:1200px;height:1px;background:#4a4848}
.copyright{position:absolute;left:99px;top:255px;font-size:12px}
.abn{position:absolute;left:981px;top:255px;font-size:12px}
</style>
</head>
<body>

<div class="abs header-band"></div>

<div class="abs logo">
  <div class="logo-mark"></div>
  <div class="logo-name">Brightcoat Painting</div>
</div>

<div class="abs phone">
  <svg width="26" height="26" viewBox="0 0 26 26"><circle cx="13" cy="13" r="11.5" fill="none" stroke="#4fa8e0" stroke-width="2"/><path d="M9 7.5l2.5 0 1 3-1.6 1.2a8 8 0 0 0 3.4 3.4l1.2-1.6 3 1v2.5c0 .8-.7 1.4-1.5 1.3A11 11 0 0 1 7.7 9c-.1-.8.5-1.5 1.3-1.5z" fill="#4fa8e0"/></svg>
  1300 555 218
</div>

<ul class="abs nav">
  <li class="active">HOME</li>
  <li>SERVICES</li>
  <li>GALLERY</li>
  <li>CONTACT US</li>
</ul>

<section class="abs hero">
  <svg class="hero-photo" width="620" height="397" role="img" aria-label="Smiling painter in cap holding a paint roller in a bright white room">
    <defs><linearGradient id="heroGrad" x1="0" y1="0" x2="1" y2="1"><stop offset="0" stop-color="#f2f4f5"/><stop offset=".5" stop-color="#d9dcdc"/><stop offset="1" stop-color="#c8b9a6"/></linearGradient></defs>
    <polygon points="0,0 617,0 478,397 0,397" fill="url(#heroGrad)"/>
  </svg>
  <h1 class="hero-title">Brightcoat <span>Painting</span></h1>
  <p class="hero-text">Neque porro quisquam est qui dolorem ipsum quia dolor sit amet, consectetur, adipisci velit</p>
  <div class="hero-btn">Learn More
    <svg width="16" height="16" viewBox="0 0 16 16"><circle cx="8" cy="8" r="8" fill="#ffffff"/><path d="M6.5 4.5L10 8l-3.5 3.5" stroke="#4fa8e0" stroke-width="2" fill="none"/></svg>
  </div>
  <div class="hero-dots"><i></i><i></i><i></i><i></i></div>
</section>

<h2 class="abs section-title" style="top:579px">OUR SERVICES</h2>

<article class="abs service" style="left:100px">
  <div class="service-photo" role="img" aria-label="Painted white weatherboard home" style="background:linear-gradient(#6f9fd6,#e6e9ea 55%,#8c8c86)"></div>
  <h3 class="service-name">Domestic Painting</h3>
  <p class="service-text">At brightcoat painting we are focused on superior quality and workmanship</p>
</article>
<article class="abs service" style="left:352px">
  <div class="service-photo" role="img" aria-label="Commercial building with signage and hedges" style="background:linear-gradient(#3f78c4,#8aa6b7 50%,#5f7a4a)"></div>
  <h3 class="service-name">Commercial Painting</h3>
  <p class="service-text">We value timeliness and organisation, because we understand that your time is valuable</p>
</article>
<article class="abs service" style="left:605px">
  <div class="service-photo" role="img" aria-label="Industrial site entrance with palm trees" style="background:linear-gradient(#8fb6d8,#9aa59a 50%,#6b7860)"></div>
  <h3 class="service-name">Industrial Painting</h3>
  <p class="service-text">We are committed to long-term relationships, so that you can expect the best</p>
</article>
<article class="abs service" style="left:856px">
  <div class="service-photo" role="img" aria-label="Red brick heritage school building" style="background:linear-gradient(90deg,#9a3b2f,#7d4a3a 55%,#4f6b3b)"></div>
  <h3 class="service-name">Heritage Painting</h3>
  <p class="service-text">We are committed to an unmatched attention to detail to ensure an outstanding result</p>
</article>

<section class="abs quality">
  <div class="stars">
    <svg width="160" height="22" viewBox="0 0 160 22">
      <g fill="#1f4a66">
        <polygon points="11,0 14,8 22,8 15.5,13 18,21 11,16 4,21 6.5,13 0,8 8,8"/>
        <polygon transform="translate(34 0)" points="11,0 14,8 22,8 15.5,13 18,21 11,16 4,21 6.5,13 0,8 8,8"/>
        <polygon transform="translate(68 0)" points="11,0 14,8 22,8 15.5,13 18,21 11,16 4,21 6.5,13 0,8 8,8"/>
        <polygon transform="translate(102 0)" points="11,0 14,8 22,8 15.5,13 18,21 11,16 4,21 6.5,13 0,8 8,8"/>
        <polygon transform="translate(136 0)" points="11,0 14,8 22,8 15.5,13 18,21 11,16 4,21 6.5,13 0,8 8,8"/>
      </g>
    </svg>
  </div>
  <h2>Quality and Service</h2>
  <p>Brightcoat Painting Services is a Melbourne family owned Painting &amp; Decorating business based in Elmsford, in the south east of Melbourne. We proudly provide domestic and commercial painting services across all suburbs of metropolitan Melbourne.</p>
</section>

<section class="abs gallery">
  <h2 class="gallery-title">PHOTO GALLERY</h2>
  <div class="gallery-main" role="img" aria-label="Interior with timber lined walls, brick wall and exposed ceiling beams" style="background:linear-gradient(#7a5a3a 0,#a27a4c 35%,#c79a5c 70%,#8e6a48)"></div>
  <div class="gallery-shadow"></div>
  <svg class="arrow" style="left:42px" width="14" height="20"><path d="M11 3L4 10l7 7" stroke="#111" stroke-width="3" fill="none"/></svg>
  <div class="thumb" style="left:73px;background:#5d3a30" role="img" aria-label="Brick room interior"></div>
  <div class="thumb" style="left:182px;background:#b9b3a8" role="img" aria-label="Kitchen cabinets"></div>
  <div class="thumb" style="left:291px;background:#8a5a36" role="img" aria-label="Timber door"></div>
  <div class="thumb" style="left:400px;background:#9a6a3e" role="img" aria-label="Timber panelling"></div>
  <div class="thumb" style="left:509px;background:#8e3a2e" role="img" aria-label="Roof painting in progress"></div>
  <div class="thumb" style="left:618px;background:#9a6a5a" role="img" aria-label="Brick house exterior"></div>
  <svg class="arrow" style="left:732px" width="14" height="20"><path d="M3 3l7 7-7 7" stroke="#111" stroke-width="3" fill="none"/></svg>
</section>

<div class="abs partner" style="left:180px;width:110px"><span style="width:14px;height:14px;background:#f2d300"></span>tradeleafs</div>
<div class="abs partner" style="left:300px;width:105px">Tintwell</div>
<div class="abs partner" style="left:440px;width:130px">Colourmark</div>
<div class="abs partner" style="left:635px;width:135px">Hollis Paints</div>
<div class="abs partner" style="left:811px;width:68px" role="img" aria-label="Workmanship warranty certificate"><span style="width:60px;height:60px;background:var(--badge);border-radius:50%"></span></div>
<div class="abs partner" style="left:915px;width:115px"><span style="width:14px;height:14px;background:#1aa0dc"></span>nearbyfind</div>

<footer class="abs footer">
  <h4 style="left:99px">Menu Links</h4>
  <ul style="left:99px"><li>Home</li><li>Services</li><li>Gallery</li><li>Contact Us</li></ul>

  <h4 style="left:281px">Other Links</h4>
  <ul style="left:281px"><li>Terms &amp; Conditions</li><li>Legal Notice</li><li>Disclaimer</li></ul>

  <h4 style="left:548px">Contact Us</h4>
  <ul class="contact-list" style="left:548px">
    <li><svg width="14" height="10"><rect x=".5" y=".5" width="13" height="9" fill="#fff"/><path d="M.5 .5L7 5l6.5-4.5" stroke="#363434" fill="none"/></svg>Email : info@brightcoatpainting.com.au</li>
    <li><svg width="14" height="14"><rect x="1" y="1" width="12" height="12" fill="#fff"/><circle cx="7" cy="7" r="2.5" fill="#363434"/></svg>Address : Elmsford, Victoria 3999, Australia</li>
    <li><svg width="14" height="14" viewBox="0 0 14 14"><path d="M2 1h3l1 3-1.5 1.2a7 7 0 0 0 3.3 3.3L9 7l3 1v3c0 .8-.7 1.3-1.4 1.2A11 11 0 0 1 1 2.4C.9 1.7 1.3 1 2 1z" fill="#fff"/></svg>Phone : 1300 555 218</li>
  </ul>
  <div class="quote-btn">Free Quotes</div>

  <h4 style="left:921px">Connect With Us</h4>
  <ul class="social" style="left:921px"><li>Facepage<i></i></li><li>Chirper<i></i></li><li>Linkpro<i></i></li></ul>

  <div class="footer-rule"></div>
  <p class="copyright">©2014 Company Name ,All Rights Reserved</p>
  <p class="abn">ABN. 12 345 678 901</p>
</footer>

</body>
</html>
```